Website Design for my Copper Distillation Equipment Business Nature Sciencey Theme

I already have a website www.cascobrewworks.com and its a sitevelo website builder one. But I cannot get the design right at all. I need this fixed.

I have logo. I need a redesign, for my website, the home page, that maybe I can have something similar in design- I can use as template to copy, for other pages so the whole thing matches? Look at my website so you understand I have a few pages...but most are links. Its a competition. Code has to be easy for me to implement, I am not expert.

Your advice needed..It would be a plus if I can update this myself throughout time. If I could have this explained to me too, the maintenance of it...how would I do this too..etc..pretend I am a child when you explain, if you can. I am not good with this stuff but I am smart and can learn fast.

I want a high end look. Maybe like an ivy league college-y look too, real preppy, chemistry...science-y, nature like is good, leaves, drops water, fields of wheat, lavender, etc.

I want every page to look similar, but the home page is what I want to be the main showpiece,..and I want each page have a little text section, maybe a photos section and a video section, for that market. Like a nice website. If I am not doing this right, let me know. I can work with you. Just help me, please. Let me know if I am doing this right.

When I pick my winning design, for my website, I will hire the artist one-on-one to re-design my shopping cart next. Or if I need additional help with implementing this current design, I can hire the same artist again too. I have a blog that I may want to hire the redesign as well too, but later on. My point is I am not just looking for one project here but I want to follow up with winning artist. So it would be return business for the winner.

I got my logo done here so I am repeat customer. And I have given that winning artist other design work.

Target Market(s)

Moonshine Stills I sell most, Essential Oil Business, Micro and Craft Distilleries, Canna-businesses, Alcohol Fuel

Industry/Entity Type

Business

Number of Pages Required

5+ page

Colors
ec1f27

Requirements
Must have
• The categories for the stills must be prominent and eye catching. The main photo I would like to be naturelike theme, but you can try out different things with me. I am open to ideas and suggestions. I would like this to be implemented easy and fast.
Nice to have
• My logo in it. You can use any of my photos as well from my pictoshare account. https://www.pictoshare.com/photos/81724596@K09/
• Colors of my Logo...matching design.
• Maybe some basic stock photos you see would match for me..
• Chemistry like symbols for the categories, I love that.

```html
<!DOCTYPE html>
<html lang="en">
<head>
<meta charset="utf-8">
<title>Casco Brew Works — Copper Stills</title>
<link rel="stylesheet" href="https://fonts.googleapis.com/css2?family=Open+Sans:wght@400;600;700&family=Raleway:wght@400;500&display=swap">
<style>
:root{
  --maroon:#4a1614;
  --maroon-deep:#3a100f;
  --cream:#ebe9e2;
  --white:#ffffff;
  --ink:#1e1e1e;
  --body:#555555;
  --muted:#8a8a86;
  --footer:#2b2b2b;
  --footer-text:#e6e6e6;
  --btn:#ecebea;
}
*{margin:0;padding:0;box-sizing:border-box}
html,body{width:789px;height:1200px;overflow:hidden}
body{position:relative;background:var(--white);font-family:"Open Sans",Arial,sans-serif;color:var(--ink)}
a{color:inherit;text-decoration:none}

.site-header{position:absolute;left:0;top:0;width:789px;height:54px;background:var(--maroon)}
.brand{position:absolute;left:38px;top:8px;display:flex;align-items:center;gap:6px;color:var(--white);font-weight:700;font-size:13px;height:38px}
.brand-mark{width:9px;height:9px;background:var(--white)}
.main-nav{position:absolute;right:48px;top:21px;display:flex;gap:16px}
.main-nav a{color:var(--white);font-size:10px;font-weight:700;line-height:12px}

.hero-band{position:absolute;left:0;top:54px;width:789px;height:453px;background:var(--cream)}
.category-prompt{position:absolute;left:241px;top:17px;font-family:"Raleway",Arial,sans-serif;font-size:12.5px;color:var(--muted)}
.category-strip{position:absolute;left:42px;top:48px;width:704px;height:76px;display:flex}
.category{position:relative;flex:1;border-right:1px solid var(--white);overflow:hidden}
.category:last-child{border-right:none}
.category-photo{position:absolute;inset:0}
.category-label{position:absolute;left:0;right:0;bottom:0;height:24px;background:rgba(40,20,15,.62);color:var(--white);font-size:10.5px;line-height:24px;padding-left:9px;white-space:nowrap}
.strip-arrow{position:absolute;top:98px;width:11px;height:26px;background:var(--maroon-deep);display:flex;align-items:center;justify-content:center}
.strip-arrow.prev{left:31px}
.strip-arrow.next{left:748px}
.hero-slide{position:absolute;left:30px;top:126px;width:728px;height:314px;background:linear-gradient(160deg,#3f5a2e 0%,#6f7d52 35%,#8a6a48 60%,#b8a98d 100%)}
.slider-dots{position:absolute;left:361px;top:416px;display:flex;gap:4px}
.slider-dots span{width:11px;height:11px;border-radius:50%;background:rgba(255,255,255,.6)}
.slider-dots span.active{background:var(--maroon);border:2px solid var(--white)}

.intro{position:absolute;left:48px;top:533px;width:392px}
.intro h1{font-family:"Raleway",Arial,sans-serif;font-weight:500;font-size:15px;line-height:18px;color:var(--ink);margin-bottom:10px}
.intro p{font-size:8px;line-height:16px;color:var(--body)}
.btn-more{position:absolute;left:48px;top:683px;width:68px;height:23px;background:var(--btn);border:1px solid #dcdad6;font-size:8.5px;font-weight:600;color:var(--ink);display:flex;align-items:center;justify-content:center}
.video{position:absolute;left:462px;top:537px;width:278px;height:169px;background:linear-gradient(180deg,#3c5a3a 0%,#7d8a6a 45%,#a9a291 75%,#8f8b82 100%)}
.video-bar{position:absolute;left:0;bottom:0;width:100%;height:14px;background:rgba(0,0,0,.85)}
.video-progress{position:absolute;left:0;top:0;width:6px;height:2px;background:#d22}

.products{position:absolute;left:48px;top:752px;display:flex;gap:18px}
.product{width:160px;position:relative;height:266px}
.product-frame{width:160px;height:199px;border:1px solid #ddd;padding:5px;background:var(--white)}
.product-photo{width:100%;height:100%}
.product-title{margin-top:11px;font-size:9.5px;font-weight:400;line-height:12px;color:var(--ink)}
.btn-buy{position:absolute;left:0;top:241px;width:40px;height:24px;border:2px solid var(--maroon);font-size:8.5px;font-weight:400;display:flex;align-items:center;justify-content:center;color:var(--ink)}

.site-footer{position:absolute;left:0;top:1070px;width:789px;height:130px;background:var(--footer);color:var(--footer-text)}
.footer-phone{position:absolute;left:279px;top:26px;font-size:9px}
.footer-brand{position:absolute;left:366px;top:24px;display:flex;align-items:center;gap:5px;font-size:11px;font-weight:700;color:var(--white)}
.footer-brand .brand-mark{width:8px;height:8px}
.footer-email{position:absolute;left:444px;top:26px;font-size:9px}
.footer-nav{position:absolute;left:183px;top:73px;display:flex;gap:14px}
.footer-nav a{font-size:9.5px;font-weight:700;color:var(--white)}
.copyright{position:absolute;left:0;width:100%;top:106px;text-align:center;font-size:9px}
</style>
</head>
<body>

<header class="site-header">
  <a class="brand" href="#"><span class="brand-mark"></span>Casco Brew Works</a>
  <nav class="main-nav">
    <a href="#">HOME</a><a href="#">ABOUT US</a><a href="#">CONTACT US</a><a href="#">PHOTO</a><a href="#">VIDEO</a><a href="#">SHOP</a><a href="#">BLOG</a><a href="#">BOOKS</a><a href="#">LINKS</a>
  </nav>
</header>

<section class="hero-band">
  <p class="category-prompt">Please Choose the Category of the Still you are looking for..</p>
  <a class="strip-arrow prev" href="#"><svg width="6" height="10" viewBox="0 0 6 10"><path d="M5 1 1 5l4 4" fill="none" stroke="#fff" stroke-width="1.6"/></svg></a>
  <div class="category-strip">
    <a class="category" href="#"><div class="category-photo" role="img" aria-label="Copper still on a deck" style="background:linear-gradient(#b9b3a6,#6c5a48)"></div><span class="category-label">Stills</span></a>
    <a class="category" href="#"><div class="category-photo" role="img" aria-label="Essential oil distilling setup" style="background:linear-gradient(#7a4a30,#c8a07a)"></div><span class="category-label">Essential Oils</span></a>
    <a class="category" href="#"><div class="category-photo" role="img" aria-label="Alcohol fuel flame" style="background:linear-gradient(#2a1a10,#c87830)"></div><span class="category-label">Alcohol Fuel</span></a>
    <a class="category" href="#"><div class="category-photo" role="img" aria-label="Herbal extraction unit" style="background:linear-gradient(#a88a60,#4a4a40)"></div><span class="category-label">Cannabis</span></a>
    <a class="category" href="#"><div class="category-photo" role="img" aria-label="Steel keg boiler on grass" style="background:linear-gradient(#5c7a3a,#a8a89a)"></div><span class="category-label">Boilers</span></a>
    <a class="category" href="#"><div class="category-photo" role="img" aria-label="Home distiller on lawn" style="background:linear-gradient(#4e7a34,#8aa860)"></div><span class="category-label">Home Distillers</span></a>
    <a class="category" href="#"><div class="category-photo" role="img" aria-label="Vodka still with buckets" style="background:linear-gradient(#7a8a6a,#dedbd2)"></div><span class="category-label">Vodka Still</span></a>
  </div>
  <a class="strip-arrow next" href="#"><svg width="6" height="10" viewBox="0 0 6 10"><path d="M1 1l4 4-4 4" fill="none" stroke="#fff" stroke-width="1.6"/></svg></a>

  <div class="hero-slide" role="img" aria-label="Countertop distiller, copper column and oranges on an outdoor table"></div>
  <div class="slider-dots"><span class="active"></span><span></span><span></span><span></span><span></span></div>
</section>

<section class="intro">
  <h1>Purity comes from a direct connection with Nature...</h1>
  <p>Welcome to our Website. Are you looking for a Moonshine Still? Are you a Lavender Farm? Are you wanting to distill Essential Oils on your farm and make Hydrosols too? Do you want to make an Herbal Extraction or Tincture? Do you want to start a Home Business? Are you a Micro ( small) Distillery wanting a Set up? Are you a Race Car driver looking for alternative ways to get your Ethanol? Are you a Prepper? Are you interested in Making Alcohol in times of Survival? Do you need clean radiation free Water for your community? Do you want to support Local Farmers, get back to the Source and Nature? Are you a Canna-business or 502?</p>
</section>
<a class="btn-more" href="#">READ MORE</a>

<div class="video" role="img" aria-label="Video of a copper still running outdoors">
  <div class="video-bar"><div class="video-progress"></div></div>
</div>

<section class="products">
  <article class="product">
    <div class="product-frame"><div class="product-photo" role="img" aria-label="Copper tower on keg in a forest" style="background:linear-gradient(#8a9a70,#4a6a30)"></div></div>
    <h2 class="product-title">Copper Still -3 inch-Tower only</h2>
    <a class="btn-buy" href="#">BUY</a>
  </article>
  <article class="product">
    <div class="product-frame"><div class="product-photo" role="img" aria-label="Essential oil distiller in front of trees" style="background:linear-gradient(#2e5a2a,#4a7a3a)"></div></div>
    <h2 class="product-title">Essential Oil Distiller</h2>
    <a class="btn-buy" href="#">BUY</a>
  </article>
  <article class="product">
    <div class="product-frame"><div class="product-photo" role="img" aria-label="Copper still on a 15 gallon keg" style="background:linear-gradient(#c8c6c0,#9a8a78)"></div></div>
    <h2 class="product-title">Copper Still- with NON ELECTRIC 15 Gallon Keg</h2>
    <a class="btn-buy" href="#">BUY</a>
  </article>
  <article class="product">
    <div class="product-frame"><div class="product-photo" role="img" aria-label="Complete ethanol distilling kit beside a house" style="background:linear-gradient(#d8cba8,#8a8070)"></div></div>
    <h2 class="product-title">Distilling Alcohol Ethanol Complete Kit 3 inch</h2>
    <a class="btn-buy" href="#">BUY</a>
  </article>
</section>

<footer class="site-footer">
  <span class="footer-phone">+1 555 010 0199</span>
  <span class="footer-brand"><span class="brand-mark"></span>Casco</span>
  <span class="footer-email">info@cascobrewworks.com</span>
  <nav class="footer-nav">
    <a href="#">HOME</a><a href="#">ABOUT US</a><a href="#">CONTACT US</a><a href="#">PHOTO</a><a href="#">VIDEO</a><a href="#">SHOP</a><a href="#">BLOG</a><a href="#">BOOKS</a><a href="#">LINKS</a>
  </nav>
  <p class="copyright">© 2015 Casco Brew Works - All Rights Reserved</p>
</footer>

</body>
</html>
```